Velmora Nightclub Flyer (Updated)

Flyer for facebook, square is fine, or rectangular. Here is the text:
VELMORA
Nightclub + Lounge
presents

B2B THURSDAY
Nov 29 2018

CLUB FLOOR:
ROLF B2B GARTH
BENEDICT SALVORTE

LOUNGE:
TOBY B2B MY COUSIN
THUNDER REGGIE

Powered by KELP Acoustics
4726 8th Avenue 21+ 9pm-2am
velmorakestrel.com for VIP booth inquiries

Target Market(s)

Nightclub

Industry/Entity Type

Night Club

Font styles to use
Sans Serif

Colors

Designer to choose colors to be used in the design.

Requirements
Must have
• All the text listed, and plz keep the theme of the attached files. We want to stay consistent with the Velmora brand
Nice to have
• Try to stay with the theme from the attachments
Should not have
• Dont' stray to far from the general theme we have from the attachments

```html
<!DOCTYPE html>
<html lang="en">
<head>
<meta charset="utf-8">
<title>Velmora – B2B Thursday</title>
<link rel="stylesheet" href="https://fonts.googleapis.com/css2?family=Lato:wght@300;400;700;900&display=swap">
<style>
  :root {
    --pink: #ef1f5e;
    --pink-deep: #e01654;
    --silver: #c9ccd3;
    --lime: #d6e38c;
    --white: #ffffff;
    --panel: rgba(8, 10, 18, 0.72);
    --grey-word: #8d8f93;
  }
  html, body {
    margin: 0;
    padding: 0;
    width: 1200px;
    height: 1200px;
    overflow: hidden;
    background: #05070f;
  }
  .flyer {
    position: relative;
    width: 1200px;
    height: 1200px;
    overflow: hidden;
    font-family: "Lato", sans-serif;
    color: var(--white);
  }
  .club-photo {
    position: absolute;
    inset: 0;
    background:
      radial-gradient(ellipse at 60% 8%, rgba(60, 190, 170, 0.55), transparent 40%),
      radial-gradient(ellipse at 20% 35%, rgba(40, 150, 240, 0.55), transparent 38%),
      radial-gradient(ellipse at 55% 30%, rgba(40, 120, 90, 0.55), transparent 45%),
      radial-gradient(ellipse at 30% 75%, rgba(30, 70, 170, 0.5), transparent 45%),
      linear-gradient(180deg, #0b1f3a 0%, #0a1840 40%, #091433 70%, #050914 100%);
  }
  .headline {
    position: absolute;
    left: 56px;
    top: 40px;
    margin: 0;
    font-size: 156px;
    font-weight: 900;
    letter-spacing: 14px;
    line-height: 1;
    color: var(--pink);
    -webkit-text-stroke: 10px var(--silver);
    paint-order: stroke fill;
  }
  .subhead {
    position: absolute;
    left: 60px;
    top: 232px;
    margin: 0;
    font-size: 42px;
    font-weight: 700;
    letter-spacing: 5px;
  }
  .presents-ribbon {
    position: absolute;
    left: 60px;
    top: 310px;
    width: 545px;
    height: 90px;
  }
  .presents-ribbon span {
    position: absolute;
    inset: 0;
    display: flex;
    align-items: center;
    justify-content: center;
    font-size: 36px;
    font-weight: 400;
    letter-spacing: 9px;
    padding-bottom: 6px;
  }
  .date-plaque {
    position: absolute;
    left: 22px;
    top: 466px;
    width: 618px;
    height: 340px;
  }
  .date-plaque .text {
    position: absolute;
    inset: 0;
    display: flex;
    flex-direction: column;
    align-items: center;
    justify-content: center;
    padding-top: 8px;
  }
  .event-name {
    font-size: 62px;
    font-weight: 400;
    letter-spacing: 1px;
    line-height: 1.1;
  }
  .event-date {
    font-size: 44px;
    font-weight: 400;
    letter-spacing: 6px;
    line-height: 1.25;
  }
  .lineup-panel {
    position: absolute;
    left: 754px;
    top: 326px;
    width: 446px;
    height: 874px;
    background: var(--panel);
  }
  .stage {
    position: absolute;
    right: 48px;
    text-align: right;
    font-size: 32px;
    line-height: 46px;
    letter-spacing: 0.5px;
  }
  .stage h2 {
    margin: 0;
    font-size: 34px;
    font-weight: 400;
    color: var(--lime);
    letter-spacing: 1px;
  }
  .stage p { margin: 0; }
  .stage-lounge { top: 378px; }
  .stage-floor { top: 672px; }
  .rule {
    position: absolute;
    height: 3px;
    background: var(--pink);
  }
  .rule-panel { left: 792px; top: 600px; width: 408px; }
  .rule-footer { left: 0; top: 981px; width: 606px; }
  .footer {
    position: absolute;
    left: 58px;
    top: 1008px;
  }
  .footer .powered {
    margin: 0 0 4px;
    font-size: 36px;
    font-weight: 400;
    color: var(--lime);
    letter-spacing: 0.5px;
  }
  .footer p {
    margin: 0;
    font-size: 26px;
    line-height: 33px;
    letter-spacing: 0.5px;
  }
  .brand-mark {
    position: absolute;
    left: 790px;
    top: 900px;
    width: 370px;
    display: flex;
    flex-direction: column;
    align-items: center;
  }
  .brand-dot {
    width: 116px;
    height: 116px;
    border-radius: 50%;
    background: var(--lime);
  }
  .brand-word {
    margin-top: 26px;
    font-size: 52px;
    font-weight: 400;
    letter-spacing: 3px;
    color: var(--grey-word);
  }
</style>
</head>
<body>
<main class="flyer">
  <div class="club-photo" role="img" aria-label="Crowd on a nightclub dance floor under blue stage lights and hanging greenery"></div>

  <h1 class="headline">VELMORA</h1>
  <p class="subhead">Nightclub+Lounge</p>

  <div class="presents-ribbon">
    <svg width="545" height="90" viewBox="0 0 545 90" aria-hidden="true">
      <rect x="22" y="14" width="501" height="62" fill="var(--pink)"/>
      <rect x="6" y="4" width="18" height="82" rx="6" fill="var(--pink-deep)"/>
      <rect x="521" y="4" width="18" height="82" rx="6" fill="var(--pink-deep)"/>
    </svg>
    <span>presents</span>
  </div>

  <div class="date-plaque">
    <svg width="618" height="340" viewBox="0 0 618 340" aria-hidden="true">
      <path d="M8 8 Q309 60 610 8 Q560 170 610 332 Q309 280 8 332 Q58 170 8 8 Z"
            fill="var(--pink)" stroke="var(--silver)" stroke-width="6"/>
    </svg>
    <div class="text">
      <div class="event-name">B2B THURSDAY</div>
      <div class="event-date">Nov 29 2018</div>
    </div>
  </div>

  <section class="lineup-panel" aria-hidden="true"></section>

  <div class="stage stage-lounge">
    <h2>LOUNGE:</h2>
    <p>TOBY B2B MY COUSIN</p>
    <p>THUNDER REGGIE</p>
  </div>

  <div class="rule rule-panel"></div>

  <div class="stage stage-floor">
    <h2>CLUB FLOOR:</h2>
    <p>ROLF B2B GARTH</p>
    <p>BENEDICT SALVORTE</p>
  </div>

  <div class="brand-mark">
    <div class="brand-dot"></div>
    <div class="brand-word">VELMORA</div>
  </div>

  <div class="rule rule-footer"></div>

  <footer class="footer">
    <p class="powered">Powered by KELP Acoustics</p>
    <p>4726 8th Avenue, 21+ 9pm-2am</p>
    <p>velmorakestrel.com</p>
    <p>for VIP booth inquiries</p>
  </footer>
</main>
</body>
</html>
```